Patent Law

Need to develop a home page for a patent lawyer.

Colors should go with logo, blues...

Company Name- Velun Tresk, PLLC

Company Overview-

I am an Intellectual Property Lawyer and focus on patents, copyrights, trademarks, & trade secrets. I work with small businesses and start ups in the chemical and biotech industries.

Why Us-

I am small firm that can provide large-firm service at a reasonable price. I also can charge flat-fees for entreprenuers in certain practice areas.

Services-
Intellectual Property
Patents
Copyrights
Trademarks
Trade secrets
Healthcare Compliance
Elder law
Wills
Trusts

Website we like-
http://www.quorvantlegal.example/ - within industry!!
http://www.daltrowemiko.example/
http://ulbrixtane.example/
http://thegravelcounsel.example/

Target Market(s)

My customers will be small business, specifically small start-up companies in the chemical and biotech arena.

Industry/Entity Type

Trade

Requirements
Must have
• Colors should go with logo, blues...

```html
<!DOCTYPE html>
<html lang="en">
<head>
<meta charset="utf-8">
<title>Velun Tresk, PLLC — Intellectual Property Law</title>
<link href="https://fonts.googleapis.com/css2?family=Open+Sans:wght@400;600;700&family=Roboto+Slab:wght@700&family=Lato:wght@400;700&display=swap" rel="stylesheet">
<style>
:root{
  --blue:#1a97dd;
  --blue-dark:#0f7fc1;
  --heading-blue:#1b8ad3;
  --ink:#333;
  --ink-soft:#444;
  --topbar:#2c2c2c;
  --social:#474747;
  --footer:#393939;
  --footer-text:#e8e8e8;
  --content-bg:#f1f1f1;
  --white:#fff;
}
*{margin:0;padding:0;box-sizing:border-box}
html,body{width:1200px;height:1113px;overflow:hidden;background:var(--white)}
body{position:relative;font-family:"Open Sans",Arial,sans-serif;color:var(--ink)}
.section{position:absolute;left:0;width:1200px}
.section > *{position:absolute}

/* top bar */
.topbar{top:0;height:28px;background:var(--topbar)}
.topbar .mail{left:663px;top:8px;display:flex;align-items:center;gap:6px;font:400 10px/12px "Lato",Arial,sans-serif;color:#ddd;white-space:nowrap}
.topbar .social{left:798px;top:5px;display:flex;gap:3.5px}
.topbar .social span{width:19px;height:19px;border-radius:50%;background:var(--social);display:block}

/* header */
.header{top:28px;height:99px;background:var(--white)}
.brand{left:240px;top:40px;display:flex;align-items:center;gap:7px;font:600 12px/14px "Open Sans",Arial,sans-serif;color:#2d3f73;letter-spacing:.6px;white-space:nowrap}
.brand i{width:12px;height:12px;border-radius:50%;background:var(--blue);display:block}
.nav{left:412px;top:39px;display:flex;align-items:center;height:22px;font:400 10px/12px "Lato",Arial,sans-serif;color:#222;letter-spacing:.2px;white-space:nowrap}
.nav a{color:inherit;text-decoration:none;padding:5px 14px;border-radius:3px}
.nav a.active{background:var(--blue);color:var(--white);margin-right:0}
.cta{top:35px;height:26px;background:var(--blue);color:var(--white);border-radius:3px;font:700 12px/14px "Lato",Arial,sans-serif;display:flex;align-items:center;justify-content:center;box-shadow:0 2px 0 var(--blue-dark);white-space:nowrap}
.cta.phone{left:819px;width:91px}
.cta.map{left:916px;width:38px}

/* hero */
.hero{top:127px;height:376px;background:linear-gradient(90deg,#eaf5f9 0%,#d7edf4 35%,#aadbe9 70%,#8ecfe3 100%)}
.hero-photo{left:652px;top:8px;width:301px;height:368px;border-radius:120px 120px 0 0;background:linear-gradient(180deg,#c9cfd6 0%,#d9a891 30%,#5b6470 60%,#3e444d 100%)}
.hero h1{left:240px;top:99px;font:700 40px/48px "Roboto Slab",Georgia,serif;color:var(--heading-blue);letter-spacing:-.3px;white-space:nowrap}
.hero p{left:240px;top:196px;width:410px;font:600 12.3px/17.6px "Open Sans",Arial,sans-serif;color:var(--ink)}
.hero .btn{left:240px;top:263px;width:90px;height:33px;background:var(--blue);color:var(--white);border-radius:3px;font:700 12px/14px "Lato",Arial,sans-serif;display:flex;align-items:center;justify-content:center;box-shadow:0 2px 0 var(--blue-dark)}

/* features */
.features{top:503px;height:370px;background:var(--content-bg)}
.feature{top:29px;width:227px;text-align:center}
.feature .photo{width:227px;height:168px;border:1px solid #ddd}
.feature h2{margin-top:10px;font:400 17px/20px "Lato",Arial,sans-serif;color:var(--heading-blue);letter-spacing:.3px}
.feature .body{margin-top:3px;font:400 10px/13.1px "Open Sans",Arial,sans-serif;color:var(--ink-soft)}
.feature .body.sans{font-family:Arial,Helvetica,sans-serif;color:#222}
.feature .body p+p{margin-top:13px}
.feature ul{list-style:none}
.f1{left:240px}.f2{left:484px}.f3{left:726px}

/* footer */
.footer{top:873px;height:203px;background:var(--footer);color:var(--footer-text)}
.footer h3{font:700 12px/14px "Lato",Arial,sans-serif;color:var(--white)}
.footer p{font:400 9.5px/12.9px "Lato",Arial,sans-serif;color:var(--footer-text)}
.col-about{left:240px;top:21px;width:230px}
.col-about h3{margin-bottom:7px}
.col-about p+p{margin-top:13px}
.col-links{left:528px;top:21px}
.col-links ul{list-style:none;margin-top:7px}
.col-links li{font:400 9.5px/12px "Lato",Arial,sans-serif;height:18.7px;display:flex;align-items:flex-start;gap:4px;color:var(--footer-text)}
.col-links li::before{content:"";margin-top:2.5px;border-left:4px solid var(--white);border-top:3.5px solid transparent;border-bottom:3.5px solid transparent}
.col-posts{left:665px;top:21px;width:296px}
.post{display:flex;gap:8px;margin-top:9px}
.post+.post{margin-top:22px}
.thumb{width:61px;height:57px;flex:none;background:linear-gradient(180deg,#aab4bf,#5e6670)}
.post time{display:block;margin-top:4px;font:400 9.5px/12px "Lato",Arial,sans-serif;color:var(--blue)}

/* bottom bar */
.bottombar{top:1076px;height:37px;background:var(--white);font:400 9.5px/12px "Lato",Arial,sans-serif;color:#444;white-space:nowrap}
.copyright{left:233px;top:16px}
.copyright b{color:var(--blue);font-weight:400}
.bottom-nav{right:246px;top:16px;display:flex;gap:6px}
.bottom-nav span.sep{color:#666}
</style>
</head>
<body>

<div class="section topbar">
  <div class="mail"><svg width="11" height="8" viewBox="0 0 11 8" aria-hidden="true"><rect x="0.5" y="0.5" width="10" height="7" fill="#bbb"/><path d="M0.5 0.5 L5.5 4.5 L10.5 0.5" fill="none" stroke="#2c2c2c"/></svg>info@veluntresk.example</div>
  <div class="social" aria-label="Social links"><span></span><span></span><span></span><span></span><span></span><span></span><span></span></div>
</div>

<header class="section header">
  <div class="brand"><i></i>VELUN TRESK, PLLC</div>
  <nav class="nav"><a class="active">HOME</a><a>ABOUT US</a><a>PRACTICE AREA</a><a>LAWYERS</a><a>CONTACT US</a></nav>
  <div class="cta phone">123 456 7891</div>
  <div class="cta map">MAP</div>
</header>

<section class="section hero">
  <div class="hero-photo" role="img" aria-label="Smiling senior lawyer in grey suit giving a thumbs up"></div>
  <h1>WE PROVIDE LEGAL<br>HELP FOR YOU!</h1>
  <p>The point of using Lorem Ipsum is that it has a more-or-less normal distribution of letters, as opposed to using Content here, content here making it look like readable English.</p>
  <div class="btn">Read More</div>
</section>

<section class="section features">
  <article class="feature f1">
    <div class="photo" role="img" aria-label="Close-up of a man in dark suit and gold tie pointing forward" style="background:linear-gradient(180deg,#3a3a3a,#1c1c1c)"></div>
    <h2>WHY US?</h2>
    <div class="body sans">
      <p>Lorem ipsum dolor sit amet, consectetuer adipiscing elit, sed diam nonummy nibh euismod tincidunt ut laoreet dolore magna aliquam erat volutpat enim ad minim veniam, quis nostrud exerce.</p>
      <p>Lorem ipsum dolor sit amet, consectetuer adipiscing diam nonummy nibh euismod tincidunt..</p>
    </div>
  </article>
  <article class="feature f2">
    <div class="photo" role="img" aria-label="Young lawyer seated with a laptop in a bright office" style="background:linear-gradient(180deg,#d9dde0,#8d939a)"></div>
    <h2>WHAT WE DO</h2>
    <ul class="body"><li>Intellectual Property</li><li>Patents</li><li>Copyrights</li><li>Trademarks</li><li>Trade secrets</li><li>Healthcare Compliance</li><li>Elder law</li><li>Wills</li><li>Trusts</li></ul>
  </article>
  <article class="feature f3">
    <div class="photo" role="img" aria-label="Street map of the office location" style="background:linear-gradient(135deg,#ecebe4,#e2e0d4)"></div>
    <h2>CONTACT INFO</h2>
    <ul class="body"><li>Address: Lorum Street . ABC 123 Lorum,NYC</li><li>Phone: 2345 678 12</li><li>Fax: 12345 678 12</li></ul>
  </article>
</section>

<footer class="section footer">
  <div class="col-about">
    <h3>About Us</h3>
    <p>Sestibulum luctus ipsum id quam euismod a malesuada sapien euismot. Vesti bulum elementum interdum.</p>
    <p>Lorem ipsum dolor sit amet elit, consectetur adipiscing. Vestibulum luctus ipsum id quam euismod a malesuada sapien euismot. Vesti bulum elementum interdum.</p>
  </div>
  <div class="col-links">
    <h3>Usefull Links</h3>
    <ul><li>New resources</li><li>About our company</li><li>What we do</li><li>Latest Updates</li><li>Our blog</li><li>Newsletter</li></ul>
  </div>
  <div class="col-posts">
    <h3>Latest Post</h3>
    <div class="post"><div class="thumb" role="img" aria-label="Portrait of a lawyer in a suit"></div><p>Lorem ipsum dolor sit amet elit, and the lorum lipsum consectetur adipiscing. Vestibulum luctus ipsum id quam euismod a malesuada sapien.<time>13 January 2014</time></p></div>
    <div class="post"><div class="thumb" role="img" aria-label="Portrait of a smiling lawyer"></div><p>Lorem ipsum dolor sit amet elit, and the lorum lipsum consectetur adipiscing. Vestibulum luctus ipsum id quam euismod a malesuada sapien.<time>13 January 2014</time></p></div>
  </div>
</footer>

<div class="section bottombar">
  <div class="copyright">Copyrights 2014.<b>VELUN TRESK,PLL</b>, All Rights Reserved.</div>
  <div class="bottom-nav"><span>Home</span><span class="sep">|</span><span>About Us</span><span class="sep">|</span><span>Practice Area</span><span class="sep">|</span><span>Lawyers</span><span class="sep">|</span><span>Contact Us</span></div>
</div>

</body>
</html>
```